New App: 4 Page Design - Updated Brief

We need an indicative design for our new app 'Kit Runner', a delivery service for tools and hardware in Sydney, Australia.

Imagine a service which copies the blue print of Zolvo Meals, but for tools and Hardware. Where builders and tradespeople are stuck on-site at work and need a tool to be delivered to them on-site, same day. They can jump onto this app and in-put their address, then select an item from the catalogue and confirm the order. Once the order has been collected and due for delivery a map will show the location of the delivery driver.

We'd like 4 pages designed.

1st page) Loading page, similar to but not the same as the ZolvoMeals example attached.

2nd page) Home page - featuring the logo and some icons which direct users around the website. (Please see link to design example: https://www.zolvomeals.example/au?ref_id=a1b2c3d4-e5f6-47a8-9b0c-d1e2f3a4b5c6 )

3rd page) A page which depicts the catalogue of tools and hardware (showing generic tools available (Please see link to design example https://www.trellmart.example/products/building-hardware).

4th page) We'd like a page which shows a map, tracking the delivery, from the hardware store, to the location of the purchaser, exactly like any typical zolvo delivery service.

Please see the below website for design guidance and ideas

https://www.trellmart.example/?src=ab.cd&ref=Xy7QpLm3Rt9Vw2KsNh4Bf8JdZc6GaT1YeUo5Mi0Wq3ErPx7Ls2Dn9Hv4Ck8Fj6Bg1Az5Tm3Ry0Qu7Wp2Xo4Zi9Ke6Jl8Nb3Vc1Sd5Ph7Mf_abc

Target Market(s)

Construction industry, tradespeople

Industry/Entity Type

Construction and Tradesmen

Colors

Designer to choose colors to be used in the design.

Requirements
Must have
• Desired Colour schemes: up to the designer but no bright colours
Nice to have
• An icon bar at the bottom of the page that directs you to the various pages on the app. Example shown in the attachments
Should not have
• An exact copy of the Zolvo App

```html
<!DOCTYPE html>
<html lang="en">
<head>
<meta charset="utf-8">
<title>Kit Runner – App Screens</title>
<link href="https://fonts.googleapis.com/css2?family=Roboto:wght@400;500;700&display=swap" rel="stylesheet">
<style>
:root{
  --teal:#0b4a52;
  --teal-mid:#2f6a71;
  --teal-light:#5d8d91;
  --ink:#151a1c;
  --muted:#6b7376;
  --line:#dde2e3;
  --field:#eef0f1;
  --page:#f6f7f7;
  --white:#ffffff;
  --frame:#0d2a2e;
}
*{box-sizing:border-box;margin:0;padding:0}
html,body{width:1200px;height:1022px;overflow:hidden;background:var(--white);font-family:"Roboto",sans-serif;color:var(--ink)}
.canvas{position:relative;width:1200px;height:1022px}
.brand-title{position:absolute;left:960px;top:56px;width:205px;text-align:right;font-size:31px;font-weight:700;color:var(--teal);letter-spacing:.5px}
.section-title{position:absolute;left:386px;top:172px;font-size:26px;font-weight:400;color:var(--teal)}

.phone{position:absolute;top:243px;width:179px;border:2.5px solid var(--frame);border-radius:16px;overflow:hidden;background:var(--page)}
.status{position:absolute;left:0;right:0;top:0;height:20px;z-index:3}
.status .time{position:absolute;left:10px;top:7px;font-size:7px;font-weight:700}
.status svg{position:absolute;right:10px;top:8px}
.on-dark .status .time{color:var(--white)}

.splash{background:var(--teal)}
.splash .word{position:absolute;left:0;right:0;top:210px;text-align:center;color:var(--white);font-size:12px;font-weight:700;letter-spacing:.4px}

.band{position:absolute;left:0;top:0;width:100%;height:100px;background:var(--teal)}
.stripes{position:absolute;left:0;top:0}
.appbar{position:absolute;left:0;right:0;top:24px;height:22px;z-index:3}
.appbar .menu{position:absolute;left:11px;top:5px}
.appbar .name{position:absolute;left:32px;top:4px;font-size:12.5px;font-weight:700;letter-spacing:.3px;color:var(--teal)}
.on-dark .appbar .name{color:var(--white)}
.avatar{position:absolute;right:9px;top:3px;width:15px;height:15px;border-radius:50%;background:#8a9497;border:1.5px solid var(--white)}

.content{position:absolute;left:0;top:0;width:100%;height:100%}
.shift .content{top:6px}
.card{position:absolute;background:var(--white);border-radius:5px;box-shadow:0 1px 4px rgba(0,0,0,.08);overflow:hidden}
.card.dark{background:var(--teal)}
.cats{left:10px;top:58px;width:158px;height:78px}
.cats h3{position:absolute;left:8px;top:7px;font-size:9px;font-weight:700}
.cats .see{position:absolute;right:8px;top:9px;font-size:6.5px;color:var(--teal)}
.card.dark h3,.card.dark .see{color:var(--white)}
.cat{position:absolute;top:26px;width:30px;text-align:center}
.cat .thumb{width:30px;height:30px;border-radius:50%;border:1px solid var(--line)}
.cat span{display:block;margin-top:3px;font-size:5.3px;line-height:1.2;color:#333;margin-left:-6px;margin-right:-6px}
.card.dark .cat span{color:#d6e3e4}

.finder{left:11px;top:151px;width:157px;height:142px}
.finder h2{position:absolute;left:11px;top:14px;width:135px;font-size:10px;line-height:1.15;font-weight:700}
.card.dark.finder h2{color:var(--white)}
.field{position:absolute;left:11px;width:136px;height:24px;border-radius:3px;font-size:6.3px;color:#80888b;display:flex;align-items:center;padding-left:8px;gap:6px}
.field.addr{top:43px;background:var(--field)}
.field.when{top:73px;background:var(--white);border:1px solid var(--line);color:var(--ink)}
.field.when .chev{position:absolute;right:8px;top:9px}
.btn{position:absolute;left:11px;top:108px;width:136px;height:24px;border-radius:3px;background:var(--teal);color:var(--white);font-size:7.5px;font-weight:500;display:flex;align-items:center;justify-content:center}
.card.dark .btn{background:#000}

.heading{position:absolute;left:9px;font-size:9px;font-weight:700}
.heading-see{position:absolute;right:8px;font-size:6.5px;color:var(--teal)}
.product{position:absolute;width:55px}
.product .pic{width:55px;height:59px;border-radius:3px;border:1px solid #eceeee}
.product .title{margin-top:8px;font-size:6px;line-height:1.25;color:#333;white-space:nowrap;overflow:hidden}
.product .meta{margin-top:5px;display:flex;justify-content:space-between;align-items:center}
.product .price{font-size:7.8px;font-weight:700;color:var(--teal)}
.product .rate{font-size:4.8px;color:#333}
.shop{position:absolute;width:55px}
.shop .pic{width:55px;height:37px;border-radius:2px}
.shop .title{margin-top:5px;font-size:6px;color:#333}
.shop .dist{margin-top:2px;font-size:5px;color:var(--muted);display:flex;align-items:center;gap:2px}

.tabs{position:absolute;left:0;right:0;height:28px;display:flex;justify-content:space-around;padding:0 12px}
.tab{width:32px;text-align:center;font-size:5.3px;color:var(--muted)}
.tab svg{display:block;margin:0 auto 2px}
.tab.active{color:var(--teal)}

.headbar{position:absolute;left:0;right:0;top:24px;height:22px;z-index:3}
.circle-btn{position:absolute;top:3px;width:15px;height:15px;border-radius:50%;background:var(--white);display:flex;align-items:center;justify-content:center}
.headbar .label{position:absolute;left:32px;top:3px;font-size:11px;font-weight:500;color:var(--white)}
.badge-dot{position:absolute;right:-1px;top:-1px;width:5px;height:5px;border-radius:50%;background:var(--teal);border:.8px solid var(--white)}
.sheet{position:absolute;left:0;right:0;top:58px;bottom:0;background:var(--white);border-radius:10px 10px 0 0}

.search{position:absolute;left:13px;top:14px;width:154px;height:23px;border-radius:5px;background:var(--field);display:flex;align-items:center;padding-left:7px;gap:5px;font-size:6.3px;color:#555}
.search .mic{position:absolute;right:7px;top:6px}
.feat-h{position:absolute;left:13px;top:54px;font-size:8.7px;font-weight:700}
.feat{position:absolute;top:73px;width:55px}
.feat .pic{width:55px;height:38px;border-radius:2px}
.feat span{display:block;margin-top:3px;font-size:5.3px;line-height:1.2;color:#333}
.all-h{position:absolute;left:13px;top:141px;font-size:8.7px;font-weight:700}
.tile{position:absolute;width:74px;background:var(--white);border-radius:3px;box-shadow:0 1px 3px rgba(0,0,0,.12);overflow:hidden}
.tile .pic{width:74px}
.tile span{display:block;padding:0 3px;margin-top:6px;text-align:center;font-size:6.2px;line-height:1.2;font-weight:500}

.eta{position:absolute;left:16px;top:24px;font-size:12.5px;font-weight:700}
.eta-sub{position:absolute;left:16px;top:39px;font-size:7.5px;color:var(--muted)}
.eta-sub b{color:var(--ink);font-weight:500}
.map{position:absolute;left:10px;top:54px;width:156px;height:232px;border-radius:4px;background:linear-gradient(160deg,#e9ebec 0%,#dfe3e4 60%,#d7dedc 100%)}
.vehicle{position:absolute;left:88px;top:22px;width:67px;height:24px;border-radius:3px;background:#1d2224;color:var(--white);padding:4px 0 0 28px}
.vehicle small{display:block;font-size:4.3px;color:#c9cfd0}
.vehicle b{display:block;font-size:6.5px;font-weight:500}
.vehicle i{position:absolute;left:5px;top:4px;width:17px;height:17px;border-radius:50%;background:var(--white)}
.driver{position:absolute;left:16px;top:245px;width:144px;height:36px;background:var(--white);border-radius:4px;box-shadow:0 1px 4px rgba(0,0,0,.15)}
.driver .face{position:absolute;left:6px;top:7px;width:22px;height:22px;border-radius:50%;background:#6d8b92}
.driver .role{position:absolute;left:35px;top:7px;font-size:5.4px;color:var(--muted)}
.driver .who{position:absolute;left:35px;top:14px;font-size:7.5px;font-weight:700}
.driver .stars{position:absolute;left:35px;top:24px;font-size:4.8px;letter-spacing:.4px}
.driver .view{position:absolute;right:6px;top:14px;font-size:5.8px;color:var(--teal);display:flex;align-items:center;gap:3px}
.msg{position:absolute;left:10px;top:296px;width:128px;height:23px;border-radius:4px;background:var(--field);font-size:6.3px;color:#444;padding:8px 0 0 7px}
.msg svg{position:absolute;right:7px;top:6px}
.call{position:absolute;left:144px;top:296px;width:22px;height:23px;border-radius:4px;background:var(--field);display:flex;align-items:center;justify-content:center}
</style>
</head>
<body>
<div class="canvas">
  <div class="brand-title">KIT RUNNER</div>
  <div class="section-title">3 Homepage designs</div>

  <!-- Splash -->
  <section class="phone splash on-dark" style="left:28px;height:391px">
    <div class="status"><span class="time">9:41</span>
      <svg width="26" height="6" viewBox="0 0 26 6"><rect x="0" y="4" width="1.3" height="2" fill="#fff"/><rect x="2" y="3" width="1.3" height="3" fill="#fff"/><rect x="4" y="1.5" width="1.3" height="4.5" fill="#fff"/><path d="M9 2.4a4 4 0 0 1 6 0M10.3 3.7a2 2 0 0 1 3.4 0" stroke="#fff" stroke-width=".9" fill="none"/><circle cx="12" cy="5.2" r=".7" fill="#fff"/><rect x="17.5" y="1" width="8" height="4.4" rx="1" fill="#fff"/></svg>
    </div>
    <div class="word">KIT RUNNER...</div>
  </section>

  <!-- Home A : teal header -->
  <section class="phone home on-dark" style="left:221px;height:577px">
    <div class="band">
      <svg class="stripes" width="179" height="100" viewBox="0 0 179 100"><polygon points="112,0 142,0 104,100 74,100" fill="var(--teal-mid)"/><polygon points="150,0 179,0 179,100 112,100" fill="var(--teal-light)" opacity=".65"/></svg>
    </div>
    <div class="status"><span class="time">9:41</span>
      <svg width="26" height="6" viewBox="0 0 26 6"><rect x="0" y="4" width="1.3" height="2" fill="#fff"/><rect x="2" y="3" width="1.3" height="3" fill="#fff"/><rect x="4" y="1.5" width="1.3" height="4.5" fill="#fff"/><path d="M9 2.4a4 4 0 0 1 6 0M10.3 3.7a2 2 0 0 1 3.4 0" stroke="#fff" stroke-width=".9" fill="none"/><circle cx="12" cy="5.2" r=".7" fill="#fff"/><rect x="17.5" y="1" width="8" height="4.4" rx="1" fill="#fff"/></svg>
    </div>
    <div class="appbar">
      <svg class="menu" width="10" height="9" viewBox="0 0 10 9"><path d="M0 1h10M0 4.5h10M0 8h10" stroke="#fff" stroke-width="1.1"/></svg>
      <span class="name">KIT RUNNER</span><span class="avatar" role="img" aria-label="User profile photo"></span>
    </div>
    <div class="content">
      <div class="card cats">
        <h3>Categories</h3><span class="see">See All</span>
        <div class="cat" style="left:7px"><div class="thumb" role="img" aria-label="General hardware photo" style="background:linear-gradient(135deg,#a9aeae,#6c7274)"></div><span>General<br>Hardware</span></div>
        <div class="cat" style="left:45px"><div class="thumb" role="img" aria-label="Fasteners photo" style="background:linear-gradient(135deg,#5d6e72,#b9c0bd)"></div><span>Fasteners<br>&amp; Fixings</span></div>
        <div class="cat" style="left:82px"><div class="thumb" role="img" aria-label="Concrete work photo" style="background:linear-gradient(135deg,#c9bfae,#8d8679)"></div><span>Concrete &amp;<br>Cementing</span></div>
        <div class="cat" style="left:120px"><div class="thumb" role="img" aria-label="Door hardware photo" style="background:linear-gradient(135deg,#f1f1f0,#b9bab8)"></div><span>Door<br>Hardware</span></div>
      </div>
      <div class="card finder">
        <h2>Find and order tools and hardware</h2>
        <div class="field addr"><svg width="7" height="8" viewBox="0 0 7 8"><path d="M3.5 8S0 4.8 0 3a3.5 3.5 0 0 1 7 0c0 1.8-3.5 5-3.5 5z" fill="#222"/><circle cx="3.5" cy="3" r="1.2" fill="#eef0f1"/></svg>Enter delivery address</div>
        <div class="field when"><svg width="7" height="7" viewBox="0 0 7 7"><circle cx="3.5" cy="3.5" r="3.5" fill="#222"/><path d="M3.5 1.6v2h1.4" stroke="#fff" stroke-width=".7" fill="none"/></svg>Deliver now<svg class="chev" width="7" height="5" viewBox="0 0 7 5"><path d="M.5 1l3 3 3-3" stroke="#222" stroke-width="1" fill="none"/></svg></div>
        <div class="btn">Find Tools</div>
      </div>
      <div class="heading" style="top:307px">Products we recommend</div>
      <div class="product" style="left:9px;top:326px"><div class="pic" role="img" aria-label="Paint tin photo" style="background:linear-gradient(160deg,#3a4a55,#1d2328)"></div><div class="title">Harlow Coat 10L<br>Heavy Duty Glos...</div><div class="meta"><span class="price">$248.90</span><span class="rate">★ 4.5</span></div></div>
      <div class="product" style="left:68px;top:326px"><div class="pic" role="img" aria-label="Cordless drill set photo" style="background:linear-gradient(160deg,#f4f5f5,#4f9aa4 55%,#222 90%)"></div><div class="title">Torvak 18V 2<br>Piece Brushless...</div><div class="meta"><span class="price">$299</span><span class="rate">★ 4.5</span></div></div>
      <div class="product" style="left:128px;top:326px"><div class="pic" role="img" aria-label="Steel shelving unit photo" style="background:linear-gradient(160deg,#fafafa,#c9cccd)"></div><div class="title">Ridgeline 190<br>x 1900 x 540mm</div><div class="meta"><span class="price">$203.47</span><span class="rate">★ 4.5</span></div></div>
      <div class="heading" style="top:436px">Shops near you</div><span class="heading-see" style="top:438px">See All</span>
      <div class="shop" style="left:9px;top:454px"><div class="pic" role="img" aria-label="Hardware store aisle photo" style="background:linear-gradient(120deg,#6d6b55,#c8b24a 50%,#4b4a3f)"></div><div class="title">Lorem Ipsum</div><div class="dist"><svg width="4" height="5" viewBox="0 0 7 8"><path d="M3.5 8S0 4.8 0 3a3.5 3.5 0 0 1 7 0c0 1.8-3.5 5-3.5 5z" fill="var(--teal)"/></svg>3 km</div></div>
      <div class="shop" style="left:68px;top:454px"><div class="pic" role="img" aria-label="Hardware store aisle photo" style="background:linear-gradient(120deg,#6d6b55,#c8b24a 50%,#4b4a3f)"></div><div class="title">Lorem Ipsum</div><div class="dist"><svg width="4" height="5" viewBox="0 0 7 8"><path d="M3.5 8S0 4.8 0 3a3.5 3.5 0 0 1 7 0c0 1.8-3.5 5-3.5 5z" fill="var(--teal)"/></svg>3 km</div></div>
      <div class="shop" style="left:128px;top:454px"><div class="pic" role="img" aria-label="Hardware store aisle photo" style="background:linear-gradient(120deg,#6d6b55,#c8b24a 50%,#4b4a3f)"></div><div class="title">Lorem Ipsum</div><div class="dist"><svg width="4" height="5" viewBox="0 0 7 8"><path d="M3.5 8S0 4.8 0 3a3.5 3.5 0 0 1 7 0c0 1.8-3.5 5-3.5 5z" fill="var(--teal)"/></svg>3 km</div></div>
    </div>
    <nav class="tabs" style="top:544px">
      <div class="tab active"><svg width="10" height="10" viewBox="0 0 10 10"><path d="M1 4.5L5 1l4 3.5V9H1z" stroke="currentColor" fill="none" stroke-width="1"/></svg>Home</div>
      <div class="tab"><svg width="10" height="10" viewBox="0 0 10 10"><circle cx="4.5" cy="4.5" r="3.5" stroke="currentColor" fill="none"/><path d="M7 7l2 2" stroke="currentColor"/></svg>Browse</div>
      <div class="tab"><svg width="10" height="10" viewBox="0 0 10 10"><path d="M1 2h1.5l1 5h4.5l1-3.5H3" stroke="currentColor" fill="none" stroke-width=".9"/><circle cx="7.5" cy="2" r="2" fill="var(--teal)"/></svg>Basket</div>
      <div class="tab"><svg width="10" height="10" viewBox="0 0 10 10"><path d="M5 .8l3.6 2.1v4.2L5 9.2 1.4 7.1V2.9z" stroke="currentColor" fill="none" stroke-width=".9"/><circle cx="5" cy="5" r="1.4" stroke="currentColor" fill="none" stroke-width=".9"/></svg>Setting</div>
    </nav>
  </section>

  <!-- Home B : teal categories card -->
  <section class="phone home shift" style="left:414px;height:577px">
    <div class="status"><span class="time">9:41</span>
      <svg width="26" height="6" viewBox="0 0 26 6"><rect x="0" y="4" width="1.3" height="2" fill="#111"/><rect x="2" y="3" width="1.3" height="3" fill="#111"/><rect x="4" y="1.5" width="1.3" height="4.5" fill="#111"/><path d="M9 2.4a4 4 0 0 1 6 0M10.3 3.7a2 2 0 0 1 3.4 0" stroke="#111" stroke-width=".9" fill="none"/><circle cx="12" cy="5.2" r=".7" fill="#111"/><rect x="17.5" y="1" width="8" height="4.4" rx="1" fill="#111"/></svg>
    </div>
    <div class="appbar">
      <svg class="menu" width="10" height="9" viewBox="0 0 10 9"><path d="M0 1h10M0 4.5h10M0 8h10" stroke="var(--teal)" stroke-width="1.1"/></svg>
      <span class="name">KIT RUNNER</span><span class="avatar" role="img" aria-label="User profile photo"></span>
    </div>
    <div class="content">
      <div class="card cats dark">
        <svg class="stripes" width="158" height="78" viewBox="0 0 158 78"><polygon points="110,0 138,0 108,78 80,78" fill="var(--teal-mid)"/><polygon points="138,0 158,0 158,78 108,78" fill="var(--teal-light)" opacity=".55"/></svg>
        <h3>Categories</h3><span class="see">See All</span>
        <div class="cat" style="left:7px"><div class="thumb" role="img" aria-label="General hardware photo" style="background:linear-gradient(135deg,#a9aeae,#6c7274)"></div><span>General<br>Hardware</span></div>
        <div class="cat" style="left:45px"><div class="thumb" role="img" aria-label="Fasteners photo" style="background:linear-gradient(135deg,#5d6e72,#b9c0bd)"></div><span>Fasteners<br>&amp; Fixings</span></div>
        <div class="cat" style="left:82px"><div class="thumb" role="img" aria-label="Concrete work photo" style="background:linear-gradient(135deg,#c9bfae,#8d8679)"></div><span>Concrete &amp;<br>Cementing</span></div>
        <div class="cat" style="left:120px"><div class="thumb" role="img" aria-label="Door hardware photo" style="background:linear-gradient(135deg,#f1f1f0,#b9bab8)"></div><span>Door<br>Hardware</span></div>
      </div>
      <div class="card finder">
        <h2>Find and order tools and hardware</h2>
        <div class="field addr"><svg width="7" height="8" viewBox="0 0 7 8"><path d="M3.5 8S0 4.8 0 3a3.5 3.5 0 0 1 7 0c0 1.8-3.5 5-3.5 5z" fill="#222"/><circle cx="3.5" cy="3" r="1.2" fill="#eef0f1"/></svg>Enter delivery address</div>
        <div class="field when"><svg width="7" height="7" viewBox="0 0 7 7"><circle cx="3.5" cy="3.5" r="3.5" fill="#222"/><path d="M3.5 1.6v2h1.4" stroke="#fff" stroke-width=".7" fill="none"/></svg>Deliver now<svg class="chev" width="7" height="5" viewBox="0 0 7 5"><path d="M.5 1l3 3 3-3" stroke="#222" stroke-width="1" fill="none"/></svg></div>
        <div class="btn">Find Tools</div>
      </div>
      <div class="heading" style="top:307px">Products we recommend</div>
      <div class="product" style="left:9px;top:326px"><div class="pic" role="img" aria-label="Paint tin photo" style="background:linear-gradient(160deg,#3a4a55,#1d2328)"></div><div class="title">Harlow Coat 10L<br>Heavy Duty Glos...</div><div class="meta"><span class="price">$248.90</span><span class="rate">★ 4.5</span></div></div>
      <div class="product" style="left:68px;top:326px"><div class="pic" role="img" aria-label="Cordless drill set photo" style="background:linear-gradient(160deg,#f4f5f5,#4f9aa4 55%,#222 90%)"></div><div class="title">Torvak 18V 2<br>Piece Brushless...</div><div class="meta"><span class="price">$299</span><span class="rate">★ 4.5</span></div></div>
      <div class="product" style="left:128px;top:326px"><div class="pic" role="img" aria-label="Steel shelving unit photo" style="background:linear-gradient(160deg,#fafafa,#c9cccd)"></div><div class="title">Ridgeline 190<br>x 1900 x 540mm</div><div class="meta"><span class="price">$203.47</span><span class="rate">★ 4.5</span></div></div>
      <div class="heading" style="top:436px">Shops near you</div><span class="heading-see" style="top:438px">See All</span>
      <div class="shop" style="left:9px;top:454px"><div class="pic" role="img" aria-label="Hardware store aisle photo" style="background:linear-gradient(120deg,#6d6b55,#c8b24a 50%,#4b4a3f)"></div><div class="title">Lorem Ipsum</div><div class="dist"><svg width="4" height="5" viewBox="0 0 7 8"><path d="M3.5 8S0 4.8 0 3a3.5 3.5 0 0 1 7 0c0 1.8-3.5 5-3.5 5z" fill="var(--teal)"/></svg>3 km</div></div>
      <div class="shop" style="left:68px;top:454px"><div class="pic" role="img" aria-label="Hardware store aisle photo" style="background:linear-gradient(120deg,#6d6b55,#c8b24a 50%,#4b4a3f)"></div><div class="title">Lorem Ipsum</div><div class="dist"><svg width="4" height="5" viewBox="0 0 7 8"><path d="M3.5 8S0 4.8 0 3a3.5 3.5 0 0 1 7 0c0 1.8-3.5 5-3.5 5z" fill="var(--teal)"/></svg>3 km</div></div>
      <div class="shop" style="left:128px;top:454px"><div class="pic" role="img" aria-label="Hardware store aisle photo" style="background:linear-gradient(120deg,#6d6b55,#c8b24a 50%,#4b4a3f)"></div><div class="title">Lorem Ipsum</div><div class="dist"><svg width="4" height="5" viewBox="0 0 7 8"><path d="M3.5 8S0 4.8 0 3a3.5 3.5 0 0 1 7 0c0 1.8-3.5 5-3.5 5z" fill="var(--teal)"/></svg>3 km</div></div>
    </div>
    <nav class="tabs" style="top:544px">
      <div class="tab active"><svg width="10" height="10" viewBox="0 0 10 10"><path d="M1 4.5L5 1l4 3.5V9H1z" stroke="currentColor" fill="none" stroke-width="1"/></svg>Home</div>
      <div class="tab"><svg width="10" height="10" viewBox="0 0 10 10"><circle cx="4.5" cy="4.5" r="3.5" stroke="currentColor" fill="none"/><path d="M7 7l2 2" stroke="currentColor"/></svg>Browse</div>
      <div class="tab"><svg width="10" height="10" viewBox="0 0 10 10"><path d="M1 2h1.5l1 5h4.5l1-3.5H3" stroke="currentColor" fill="none" stroke-width=".9"/><circle cx="7.5" cy="2" r="2" fill="var(--teal)"/></svg>Basket</div>
      <div class="tab"><svg width="10" height="10" viewBox="0 0 10 10"><path d="M5 .8l3.6 2.1v4.2L5 9.2 1.4 7.1V2.9z" stroke="currentColor" fill="none" stroke-width=".9"/><circle cx="5" cy="5" r="1.4" stroke="currentColor" fill="none" stroke-width=".9"/></svg>Setting</div>
    </nav>
  </section>

  <!-- Home C : teal finder card -->
  <section class="phone home shift" style="left:607px;height:577px">
    <div class="status"><span class="time">9:41</span>
      <svg width="26" height="6" viewBox="0 0 26 6"><rect x="0" y="4" width="1.3" height="2" fill="#111"/><rect x="2" y="3" width="1.3" height="3" fill="#111"/><rect x="4" y="1.5" width="1.3" height="4.5" fill="#111"/><path d="M9 2.4a4 4 0 0 1 6 0M10.3 3.7a2 2 0 0 1 3.4 0" stroke="#111" stroke-width=".9" fill="none"/><circle cx="12" cy="5.2" r=".7" fill="#111"/><rect x="17.5" y="1" width="8" height="4.4" rx="1" fill="#111"/></svg>
    </div>
    <div class="appbar">
      <svg class="menu" width="10" height="9" viewBox="0 0 10 9"><path d="M0 1h10M0 4.5h10M0 8h10" stroke="var(--teal)" stroke-width="1.1"/></svg>
      <span class="name">KIT RUNNER</span><span class="avatar" role="img" aria-label="User profile photo"></span>
    </div>
    <div class="content">
      <div class="card cats">
        <h3>Categories</h3><span class="see">See All</span>
        <div class="cat" style="left:7px"><div class="thumb" role="img" aria-label="General hardware photo" style="background:linear-gradient(135deg,#a9aeae,#6c7274)"></div><span>General<br>Hardware</span></div>
        <div class="cat" style="left:45px"><div class="thumb" role="img" aria-label="Fasteners photo" style="background:linear-gradient(135deg,#5d6e72,#b9c0bd)"></div><span>Fasteners<br>&amp; Fixings</span></div>
        <div class="cat" style="left:82px"><div class="thumb" role="img" aria-label="Concrete work photo" style="background:linear-gradient(135deg,#c9bfae,#8d8679)"></div><span>Concrete &amp;<br>Cementing</span></div>
        <div class="cat" style="left:120px"><div class="thumb" role="img" aria-label="Door hardware photo" style="background:linear-gradient(135deg,#f1f1f0,#b9bab8)"></div><span>Door<br>Hardware</span></div>
      </div>
      <div class="card finder dark">
        <svg class="stripes" width="157" height="142" viewBox="0 0 157 142"><polygon points="62,0 122,0 92,142 32,142" fill="var(--teal-mid)"/><polygon points="122,0 157,0 157,142 92,142" fill="var(--teal-light)" opacity=".6"/></svg>
        <h2>Find and order tools and hardware</h2>
        <div class="field addr"><svg width="7" height="8" viewBox="0 0 7 8"><path d="M3.5 8S0 4.8 0 3a3.5 3.5 0 0 1 7 0c0 1.8-3.5 5-3.5 5z" fill="#222"/><circle cx="3.5" cy="3" r="1.2" fill="#eef0f1"/></svg>Enter delivery address</div>
        <div class="field when"><svg width="7" height="7" viewBox="0 0 7 7"><circle cx="3.5" cy="3.5" r="3.5" fill="#222"/><path d="M3.5 1.6v2h1.4" stroke="#fff" stroke-width=".7" fill="none"/></svg>Deliver now<svg class="chev" width="7" height="5" viewBox="0 0 7 5"><path d="M.5 1l3 3 3-3" stroke="#222" stroke-width="1" fill="none"/></svg></div>
        <div class="btn">Find Tools</div>
      </div>
      <div class="heading" style="top:307px">Products we recommend</div>
      <div class="product" style="left:9px;top:326px"><div class="pic" role="img" aria-label="Paint tin photo" style="background:linear-gradient(160deg,#3a4a55,#1d2328)"></div><div class="title">Harlow Coat 10L<br>Heavy Duty Glos...</div><div class="meta"><span class="price">$248.90</span><span class="rate">★ 4.5</span></div></div>
      <div class="product" style="left:68px;top:326px"><div class="pic" role="img" aria-label="Cordless drill set photo" style="background:linear-gradient(160deg,#f4f5f5,#4f9aa4 55%,#222 90%)"></div><div class="title">Torvak 18V 2<br>Piece Brushless...</div><div class="meta"><span class="price">$299</span><span class="rate">★ 4.5</span></div></div>
      <div class="product" style="left:128px;top:326px"><div class="pic" role="img" aria-label="Steel shelving unit photo" style="background:linear-gradient(160deg,#fafafa,#c9cccd)"></div><div class="title">Ridgeline 190<br>x 1900 x 540mm</div><div class="meta"><span class="price">$203.47</span><span class="rate">★ 4.5</span></div></div>
      <div class="heading" style="top:436px">Shops near you</div><span class="heading-see" style="top:438px">See All</span>
      <div class="shop" style="left:9px;top:454px"><div class="pic" role="img" aria-label="Hardware store aisle photo" style="background:linear-gradient(120deg,#6d6b55,#c8b24a 50%,#4b4a3f)"></div><div class="title">Lorem Ipsum</div><div class="dist"><svg width="4" height="5" viewBox="0 0 7 8"><path d="M3.5 8S0 4.8 0 3a3.5 3.5 0 0 1 7 0c0 1.8-3.5 5-3.5 5z" fill="var(--teal)"/></svg>3 km</div></div>
      <div class="shop" style="left:68px;top:454px"><div class="pic" role="img" aria-label="Hardware store aisle photo" style="background:linear-gradient(120deg,#6d6b55,#c8b24a 50%,#4b4a3f)"></div><div class="title">Lorem Ipsum</div><div class="dist"><svg width="4" height="5" viewBox="0 0 7 8"><path d="M3.5 8S0 4.8 0 3a3.5 3.5 0 0 1 7 0c0 1.8-3.5 5-3.5 5z" fill="var(--teal)"/></svg>3 km</div></div>
      <div class="shop" style="left:128px;top:454px"><div class="pic" role="img" aria-label="Hardware store aisle photo" style="background:linear-gradient(120deg,#6d6b55,#c8b24a 50%,#4b4a3f)"></div><div class="title">Lorem Ipsum</div><div class="dist"><svg width="4" height="5" viewBox="0 0 7 8"><path d="M3.5 8S0 4.8 0 3a3.5 3.5 0 0 1 7 0c0 1.8-3.5 5-3.5 5z" fill="var(--teal)"/></svg>3 km</div></div>
    </div>
    <nav class="tabs" style="top:544px">
      <div class="tab active"><svg width="10" height="10" viewBox="0 0 10 10"><path d="M1 4.5L5 1l4 3.5V9H1z" stroke="currentColor" fill="none" stroke-width="1"/></svg>Home</div>
      <div class="tab"><svg width="10" height="10" viewBox="0 0 10 10"><circle cx="4.5" cy="4.5" r="3.5" stroke="currentColor" fill="none"/><path d="M7 7l2 2" stroke="currentColor"/></svg>Browse</div>
      <div class="tab"><svg width="10" height="10" viewBox="0 0 10 10"><path d="M1 2h1.5l1 5h4.5l1-3.5H3" stroke="currentColor" fill="none" stroke-width=".9"/><circle cx="7.5" cy="2" r="2" fill="var(--teal)"/></svg>Basket</div>
      <div class="tab"><svg width="10" height="10" viewBox="0 0 10 10"><path d="M5 .8l3.6 2.1v4.2L5 9.2 1.4 7.1V2.9z" stroke="currentColor" fill="none" stroke-width=".9"/><circle cx="5" cy="5" r="1.4" stroke="currentColor" fill="none" stroke-width=".9"/></svg>Setting</div>
    </nav>
  </section>

  <!-- Categories -->
  <section class="phone catalogue on-dark" style="left:800px;height:622px">
    <div class="band">
      <svg class="stripes" width="179" height="100" viewBox="0 0 179 100"><polygon points="112,0 142,0 104,100 74,100" fill="var(--teal-mid)"/><polygon points="150,0 179,0 179,100 112,100" fill="var(--teal-light)" opacity=".65"/></svg>
    </div>
    <div class="status"><span class="time">9:41</span>
      <svg width="26" height="6" viewBox="0 0 26 6"><rect x="0" y="4" width="1.3" height="2" fill="#fff"/><rect x="2" y="3" width="1.3" height="3" fill="#fff"/><rect x="4" y="1.5" width="1.3" height="4.5" fill="#fff"/><path d="M9 2.4a4 4 0 0 1 6 0M10.3 3.7a2 2 0 0 1 3.4 0" stroke="#fff" stroke-width=".9" fill="none"/><circle cx="12" cy="5.2" r=".7" fill="#fff"/><rect x="17.5" y="1" width="8" height="4.4" rx="1" fill="#fff"/></svg>
    </div>
    <div class="headbar">
      <span class="circle-btn" style="left:8px"><svg width="5" height="7" viewBox="0 0 5 7"><path d="M4 .5L1 3.5 4 6.5" stroke="var(--teal)" stroke-width="1.1" fill="none"/></svg></span>
      <span class="label">Categories</span>
      <span class="circle-btn" style="left:128px"><svg width="8" height="7" viewBox="0 0 8 7"><path d="M.3 .8h1.3l.9 4h4l.8-2.8H2" stroke="var(--teal)" fill="none" stroke-width=".9"/></svg><i class="badge-dot"></i></span>
      <span class="circle-btn" style="left:149px"><svg width="2" height="8" viewBox="0 0 2 8"><circle cx="1" cy="1" r=".8" fill="var(--teal)"/><circle cx="1" cy="4" r=".8" fill="var(--teal)"/><circle cx="1" cy="7" r=".8" fill="var(--teal)"/></svg></span>
    </div>
    <div class="sheet">
      <div class="search"><svg width="7" height="7" viewBox="0 0 10 10"><circle cx="4.5" cy="4.5" r="3.5" stroke="#333" fill="none" stroke-width="1.2"/><path d="M7 7l2 2" stroke="#333" stroke-width="1.2"/></svg>Search tools and hardware...<svg class="mic" width="6" height="9" viewBox="0 0 6 9"><rect x="1.5" y=".5" width="3" height="5" rx="1.5" stroke="#333" fill="none" stroke-width=".8"/><path d="M.5 4a2.5 2.5 0 0 0 5 0M3 6.5V8.5" stroke="#333" fill="none" stroke-width=".8"/></svg></div>
      <div class="feat-h">Featured categories this week</div>
      <div class="feat" style="left:12px"><div class="pic" role="img" aria-label="Assorted power tools photo" style="background:linear-gradient(135deg,#d8c48a,#8b3b2f 50%,#3f4a50)"></div><span>Tools</span></div>
      <div class="feat" style="left:72px"><div class="pic" role="img" aria-label="Vacuum cleaner in a room photo" style="background:linear-gradient(135deg,#b9bdbf,#6b6f72)"></div><span>Vacuum &amp; Steam<br>Cleaners</span></div>
      <div class="feat" style="left:132px"><div class="pic" role="img" aria-label="Garage storage shelving photo" style="background:linear-gradient(135deg,#4e5b4f,#b48b55 50%,#3e4246)"></div><span>Storage &amp; Shelving</span></div>
      <div class="all-h">All</div>
      <div class="tile" style="left:13px;top:161px;height:67px"><div class="pic" style="height:47px;background:linear-gradient(135deg,#c9cdcd,#6c7476)" role="img" aria-label="Scaffold and wall photo"></div><span>General Hardware</span></div>
      <div class="tile" style="left:13px;top:237px;height:67px"><div class="pic" style="height:47px;background:linear-gradient(135deg,#b7b4ab,#e1ded6 60%,#8c8c86)" role="img" aria-label="Concrete being smoothed photo"></div><span>Concrete &amp; Cementing</span></div>
      <div class="tile" style="left:13px;top:312px;height:69px"><div class="pic" style="height:47px;background:linear-gradient(90deg,#a9b4bd,#dde3e8,#9aa6af,#dde3e8)" role="img" aria-label="Corrugated steel sheets photo"></div><span>Steel &amp; Aluminium<br>Section</span></div>
      <div class="tile" style="left:13px;top:388px;height:118px"><div class="pic" style="height:97px;background:linear-gradient(170deg,#e5c9a2 0%,#d3ad7e 45%,#2c2f31 75%,#46494b)" role="img" aria-label="Timber boards and drill photo"></div><span>Building Materials &amp;<br>Supplies</span></div>
      <div class="tile" style="left:93px;top:161px;height:114px"><div class="pic" style="height:97px;background:linear-gradient(160deg,#b8c6cc,#3a4043 45%,#c7c2a8 75%,#2e3335)" role="img" aria-label="Screws and brackets on a mat photo"></div><span>Fasteners &amp; Fixings</span></div>
      <div class="tile" style="left:93px;top:286px;height:66px"><div class="pic" style="height:48px;background:linear-gradient(90deg,#6f6c67 0%,#d9d8d4 30%,#f4f4f3 100%)" role="img" aria-label="Sliding barn door photo"></div><span>Door Hardware</span></div>
      <div class="tile" style="left:93px;top:362px;height:67px"><div class="pic" style="height:46px;background:linear-gradient(180deg,#a9b89a,#8aa4b0 55%,#5d86a1)" role="img" aria-label="Glass pool fence photo"></div><span>Fenching &amp; Gates</span></div>
      <div class="tile" style="left:93px;top:437px;height:67px"><div class="pic" style="height:47px;background:linear-gradient(135deg,#3a3229,#c68e4f 55%,#e0b77c)" role="img" aria-label="Timber block photo"></div><span>Timber</span></div>
      <nav class="tabs" style="top:530px">
        <div class="tab"><svg width="10" height="10" viewBox="0 0 10 10"><path d="M1 4.5L5 1l4 3.5V9H1z" stroke="currentColor" fill="none" stroke-width="1"/></svg>Home</div>
        <div class="tab active"><svg width="10" height="10" viewBox="0 0 10 10"><circle cx="4.5" cy="4.5" r="3.5" stroke="currentColor" fill="none"/><path d="M7 7l2 2" stroke="currentColor"/></svg>Browse</div>
        <div class="tab"><svg width="10" height="10" viewBox="0 0 10 10"><path d="M1 2h1.5l1 5h4.5l1-3.5H3" stroke="currentColor" fill="none" stroke-width=".9"/><circle cx="7.5" cy="2" r="2" fill="var(--teal)"/></svg>Basket</div>
        <div class="tab"><svg width="10" height="10" viewBox="0 0 10 10"><path d="M5 .8l3.6 2.1v4.2L5 9.2 1.4 7.1V2.9z" stroke="currentColor" fill="none" stroke-width=".9"/><circle cx="5" cy="5" r="1.4" stroke="currentColor" fill="none" stroke-width=".9"/></svg>Setting</div>
      </nav>
    </div>
  </section>

  <!-- Live tracking -->
  <section class="phone tracking on-dark" style="left:993px;height:391px">
    <div class="band">
      <svg class="stripes" width="179" height="100" viewBox="0 0 179 100"><polygon points="112,0 142,0 104,100 74,100" fill="var(--teal-mid)"/><polygon points="150,0 179,0 179,100 112,100" fill="var(--teal-light)" opacity=".65"/></svg>
    </div>
    <div class="status"><span class="time">9:41</span>
      <svg width="26" height="6" viewBox="0 0 26 6"><rect x="0" y="4" width="1.3" height="2" fill="#fff"/><rect x="2" y="3" width="1.3" height="3" fill="#fff"/><rect x="4" y="1.5" width="1.3" height="4.5" fill="#fff"/><path d="M9 2.4a4 4 0 0 1 6 0M10.3 3.7a2 2 0 0 1 3.4 0" stroke="#fff" stroke-width=".9" fill="none"/><circle cx="12" cy="5.2" r=".7" fill="#fff"/><rect x="17.5" y="1" width="8" height="4.4" rx="1" fill="#fff"/></svg>
    </div>
    <div class="headbar">
      <span class="circle-btn" style="left:8px"><svg width="5" height="7" viewBox="0 0 5 7"><path d="M4 .5L1 3.5 4 6.5" stroke="var(--teal)" stroke-width="1.1" fill="none"/></svg></span>
      <span class="label">Live Tracking</span>
      <span class="circle-btn" style="left:128px"><svg width="8" height="7" viewBox="0 0 8 7"><path d="M.3 .8h1.3l.9 4h4l.8-2.8H2" stroke="var(--teal)" fill="none" stroke-width=".9"/></svg><i class="badge-dot"></i></span>
      <span class="circle-btn" style="left:149px"><svg width="2" height="8" viewBox="0 0 2 8"><circle cx="1" cy="1" r=".8" fill="var(--teal)"/><circle cx="1" cy="4" r=".8" fill="var(--teal)"/><circle cx="1" cy="7" r=".8" fill="var(--teal)"/></svg></span>
    </div>
    <div class="sheet">
      <div class="eta">In 15 min</div>
      <div class="eta-sub">Estimated arrival time: <b>6.00 pm</b></div>
      <div class="map" role="img" aria-label="Street map showing the driver's route to the delivery address">
        <div class="vehicle"><i></i><small>Scooty</small><b>BAC-XXXX</b></div>
      </div>
      <div class="driver">
        <span class="face" role="img" aria-label="Driver photo"></span>
        <span class="role">Driver Name</span>
        <span class="who">Sam Vale</span>
        <span class="stars">★★★★☆</span>
        <span class="view">View Profile <svg width="4" height="6" viewBox="0 0 4 6"><path d="M.5.5L3 3 .5 5.5" stroke="currentColor" fill="none"/></svg></span>
      </div>
      <div class="msg">Send a message...<svg width="6" height="9" viewBox="0 0 6 9"><rect x="1.5" y=".5" width="3" height="5" rx="1.5" stroke="#333" fill="none" stroke-width=".8"/><path d="M.5 4a2.5 2.5 0 0 0 5 0M3 6.5V8.5" stroke="#333" fill="none" stroke-width=".8"/></svg></div>
      <div class="call"><svg width="8" height="8" viewBox="0 0 8 8"><path d="M1.6.6l1.3 1.6-.7 1a4.5 4.5 0 0 0 2.6 2.6l1-.7 1.6 1.3-.8 1C3.5 7.4.6 4.5.6 1.4z" fill="#222"/></svg></div>
    </div>
  </section>
</div>
</body>
</html>
```